Local fast-growing company in the service sector

We are looking for a modern business card design, which should also appear on our letterheads

Target Market(s)

Private and industrial sectors

Contact Information for Business Card

Vorname Name
Kellberger Str. 18
72418 Lindenthal
Tel.: 07146-839214-0
Name@agentur-kvtl.de

Colors
9d9d9d
919191
aaaaaa

Requirements
Must have
• The logo (file) in silver

```html
<!DOCTYPE html>
<html lang="de">
<head>
<meta charset="utf-8">
<title>KVTL Visitenkarte</title>
<link rel="stylesheet" href="https://fonts.googleapis.com/css2?family=Nunito+Sans:wght@400;600;700&display=swap">
<style>
  :root {
    --backdrop: #2b2b2c;
    --card-white: #ffffff;
    --silver-light: #c4c5c7;
    --silver-mid: #aaaaaa;
    --silver-dark: #7b7b7d;
    --brand-grey: #9d9d9d;
    --name-grey: #7a7a7a;
    --text-dark: #4a4a4a;
    --url-dark: #222326;
    --divider: #919191;
  }
  * { margin: 0; padding: 0; box-sizing: border-box; }
  html, body { width: 1200px; height: 960px; overflow: hidden; }
  body {
    background: var(--backdrop);
    font-family: "Nunito Sans", Arial, sans-serif;
    position: relative;
  }
  .card {
    position: absolute;
    width: 600px;
    height: 342px;
    border-radius: 22px;
    overflow: hidden;
  }
  .card--front {
    left: 302px; top: 129px;
    background: linear-gradient(90deg, var(--card-white) 0%, var(--card-white) 55%, #ededed 72%, #d2d2d2 88%, #bdbdbd 100%);
  }
  .card--back {
    left: 299px; top: 488px;
    background: linear-gradient(90deg, var(--silver-light) 0%, #b5b6b8 45%, #9a9a9c 72%, var(--silver-dark) 100%);
  }
  .brand {
    position: absolute;
    left: 66px; top: 140px;
    display: flex; align-items: center; gap: 14px;
  }
  .brand__mark {
    width: 34px; height: 34px;
    background: var(--brand-grey);
  }
  .brand__name {
    font-size: 50px; font-weight: 700;
    color: var(--brand-grey);
    letter-spacing: 1px;
    line-height: 1;
  }
  .divider {
    position: absolute;
    left: 333px; top: 101px;
    width: 2px; height: 148px;
    background: linear-gradient(180deg, rgba(145,145,145,0), var(--divider) 20%, var(--divider) 80%, rgba(145,145,145,0));
  }
  .contact {
    position: absolute;
    left: 361px; top: 101px;
    color: var(--text-dark);
  }
  .contact__name {
    font-size: 25px; font-weight: 700;
    color: var(--name-grey);
    line-height: 32px;
    margin-bottom: 2px;
  }
  .contact__address {
    font-size: 15px; line-height: 18px;
    margin-bottom: 8px;
  }
  .contact__list { list-style: none; font-size: 15px; line-height: 19px; }
  .contact__list li { display: flex; align-items: center; gap: 8px; }
  .contact__list svg { width: 13px; height: 13px; fill: var(--text-dark); flex: none; }
  .back-brand {
    position: absolute;
    left: 0; right: 0; top: 100px;
    text-align: center;
    font-size: 90px; font-weight: 700;
    color: #8e8e90;
    letter-spacing: 4px;
    line-height: 1;
  }
  .back-url {
    position: absolute;
    left: 0; right: 0; top: 289px;
    text-align: center;
    font-size: 15px;
    letter-spacing: 3px;
    color: var(--url-dark);
  }
</style>
</head>
<body>
  <section class="card card--front">
    <div class="brand">
      <span class="brand__mark"></span>
      <span class="brand__name">KVTL</span>
    </div>
    <div class="divider"></div>
    <div class="contact">
      <p class="contact__name">Vorname Name</p>
      <p class="contact__address">Kellberger Str. 18<br>72418 Lindenthal</p>
      <ul class="contact__list">
        <li>
          <svg viewBox="0 0 24 24" aria-hidden="true"><path d="M6.6 10.8a15.1 15.1 0 0 0 6.6 6.6l2.2-2.2c.3-.3.7-.4 1-.2 1.1.4 2.3.6 3.6.6.6 0 1 .4 1 1V20c0 .6-.4 1-1 1A17 17 0 0 1 3 4c0-.6.4-1 1-1h3.5c.6 0 1 .4 1 1 0 1.2.2 2.4.6 3.6.1.3 0 .7-.2 1l-2.3 2.2z"/></svg>
          07146-839214-0
        </li>
        <li>
          <svg viewBox="0 0 24 24" aria-hidden="true"><path d="M2 5h20v14H2V5zm2 2v.5l8 5 8-5V7H4z"/></svg>
          Name@agentur-kvtl.de
        </li>
        <li>
          <svg viewBox="0 0 24 24" aria-hidden="true"><path d="M12 2a10 10 0 1 0 0 20 10 10 0 0 0 0-20zm6.9 6h-3a15 15 0 0 0-1.3-3.9A8 8 0 0 1 18.9 8zM12 4c.8 1.2 1.5 2.5 1.9 4h-3.8c.4-1.5 1.1-2.8 1.9-4zM4.3 14a8 8 0 0 1 0-4h3.4a16 16 0 0 0 0 4H4.3zm.8 2h3a15 15 0 0 0 1.3 3.9A8 8 0 0 1 5.1 16zM8 8H5.1a8 8 0 0 1 4.3-3.9C8.8 5.3 8.4 6.6 8 8zm4 12c-.8-1.2-1.5-2.5-1.9-4h3.8c-.4 1.5-1.1 2.8-1.9 4zm2.3-6H9.7a14 14 0 0 1 0-4h4.6a14 14 0 0 1 0 4zm.3 5.9c.6-1.2 1-2.5 1.3-3.9h3a8 8 0 0 1-4.3 3.9zm1.7-5.9a16 16 0 0 0 0-4h3.4a8 8 0 0 1 0 4h-3.4z"/></svg>
          www.agentur-kvtl.de
        </li>
      </ul>
    </div>
  </section>

  <section class="card card--back">
    <p class="back-brand">KVTL</p>
    <p class="back-url">WWW.AGENTUR-KVTL.DE</p>
  </section>
</body>
</html>
```